Harwick + Pell Architect Marketing campaign for a morern fresh architecture cutting egde firm th...

To create en exciting template for our monthly newsletters to go out to all our clients via email. I have added a bit of an idea of what we like but not limited to..... we like a nice clean fresh look with lots of white space. I hve aslo added a sketch of the type of how we might layt it out - you may have a better idea. also the pics of the projects for the first issue (issue #1)We like the opening page like the attached brewlane had and replace the cup with apic of our building/office. Cant wait to see what you come up with.

Target Market(s)

young professionals

Industry/Entity Type

Architectural

Font styles to use
Serif

Colors

Designer to choose colors to be used in the design.

Requirements
Must have
• Logo, text information provided, photos provided
Nice to have
• lots of white space, clean and frest looking

```html
<!DOCTYPE html>
<html lang="en">
<head>
<meta charset="utf-8">
<title>Harwick + Pell Architecture — Welcome Newsletter</title>
<link rel="stylesheet" href="https://fonts.googleapis.com/css2?family=Source+Serif+4:opsz,wght@8..60,400;8..60,600;8..60,700&display=swap">
<style>
  :root {
    --page-bg: #ffffff;
    --card-bg: #ffffff;
    --ink: #1c1c1c;
    --muted: #9a9a9a;
    --rule: #e2e2e2;
    --panel: rgba(40, 40, 40, 0.78);
    --soft: #f5f5f5;
    --icon-disc: #222222;
    --badge-light: #8a8a8a;
    --badge-dark: #3f3f3f;
    --white: #ffffff;
  }
  * { box-sizing: border-box; margin: 0; padding: 0; }
  html, body {
    width: 773px; height: 1200px; overflow: hidden;
    background: var(--page-bg);
    font-family: "Source Serif 4", Georgia, serif;
    color: var(--ink);
  }
  .newsletter {
    position: absolute; left: 31px; top: 28px;
    width: 704px; height: 1140px;
    background: var(--card-bg);
  }
  .view-browser {
    position: absolute; top: 20px; right: 23px;
    font-size: 11px; color: var(--muted);
  }
  .top-rule {
    position: absolute; top: 40px; left: 17px; right: 17px;
    border-top: 1px solid var(--rule);
  }
  .brand {
    position: absolute; top: 84px; left: 0; right: 0;
    display: flex; align-items: center; justify-content: center; gap: 14px;
  }
  .brand-square { width: 44px; height: 44px; background: var(--ink); }
  .brand-name {
    font-size: 28px; font-weight: 700; letter-spacing: 2px;
    text-transform: uppercase; color: var(--ink);
  }
  .hero {
    position: absolute; left: 22px; top: 182px;
    width: 660px; height: 558px;
    background: linear-gradient(180deg,
      #c8ccd4 0%, #d9dbe0 12%, #3a3c40 22%, #2e3034 42%,
      #8b8f92 52%, #9fa3a6 62%, #7f8b70 72%, #a3a7aa 85%, #b8bcc2 100%);
  }
  .hero-panel {
    position: absolute; left: 0; top: 125px;
    width: 346px; height: 289px;
    background: var(--panel);
    padding: 26px 22px 0 25px;
    color: var(--white);
  }
  .hero-title {
    font-size: 34px; font-weight: 700; line-height: 50px;
    text-transform: uppercase; letter-spacing: 0.5px;
  }
  .hero-text {
    margin-top: 10px;
    font-size: 15px; line-height: 25px;
  }
  .experience {
    position: absolute; left: 22px; top: 750px;
    width: 660px; height: 259px;
    background: var(--soft);
  }
  .experience-title {
    position: absolute; top: 19px; left: 0; right: 0;
    text-align: center; font-size: 22px; font-weight: 400; line-height: 30px;
  }
  .feature {
    position: absolute; top: 82px; width: 206px; margin-left: -103px;
    text-align: center;
  }
  .feature:nth-of-type(1) { left: 107px; }
  .feature:nth-of-type(2) { left: 334px; }
  .feature:nth-of-type(3) { left: 547px; }
  .feature-icon {
    width: 58px; height: 58px; margin: 0 auto;
    border-radius: 50%; background: var(--icon-disc);
    display: flex; align-items: center; justify-content: center;
  }
  .feature-title {
    margin-top: 12px; font-size: 17px; font-weight: 600; line-height: 24px;
  }
  .feature-text {
    margin-top: 1px; font-size: 12px; line-height: 20px;
  }
  .footer {
    position: absolute; left: 22px; top: 1019px;
    width: 658px; height: 101px;
    border: 2px solid var(--rule);
  }
  .footer > * { position: absolute; }
  .footer-label {
    font-size: 14px; font-weight: 400; line-height: 21px;
    text-transform: uppercase; letter-spacing: 0.4px;
    top: 50%; transform: translateY(-50%);
  }
  .footer-label.connect { left: 16px; }
  .footer-label.membership { left: 301px; }
  .footer-divider {
    width: 1px; height: 50px; background: var(--rule);
    top: 50%; transform: translateY(-50%);
  }
  .footer-divider.first { left: 129px; }
  .footer-divider.second { left: 283px; }
  .social-list {
    left: 141px; top: 50%; transform: translateY(-50%);
    display: flex; gap: 8px;
  }
  .social-name { font-size: 13px; font-weight: 600; color: var(--ink); }
  .badge-round {
    left: 442px; top: 18px;
    width: 72px; height: 60px; border-radius: 8px; background: var(--badge-light);
  }
  .badge-wide {
    left: 538px; top: 32px;
    width: 90px; height: 34px; background: var(--badge-dark);
  }
</style>
</head>
<body>
  <main class="newsletter">
    <div class="view-browser">View Browser</div>
    <div class="top-rule"></div>

    <header class="brand">
      <span class="brand-square"></span>
      <span class="brand-name">Harwick + Pell</span>
    </header>

    <section class="hero" role="img" aria-label="Rendering of a modern dark-clad house with stone steps, timber deck and a boat on the water">
      <div class="hero-panel">
        <h1 class="hero-title">We’re glad<br>you’re here</h1>
        <p class="hero-text">Now that you are a Harwick + Pell Architecture insider you’ll be among the first to hear about upcoming projects that the studio is working on, completed projects, news and more.</p>
      </div>
    </section>

    <section class="experience">
      <h2 class="experience-title">Make the most of your experience</h2>
      <div class="feature">
        <div class="feature-icon">
          <svg width="22" height="22" viewBox="0 0 24 24" fill="none" stroke="#fff" stroke-width="2.4"><circle cx="12" cy="12" r="3.2"/><circle cx="12" cy="12" r="7.5" stroke-dasharray="3.6 2.3"/></svg>
        </div>
        <h3 class="feature-title">Icon Text here</h3>
        <p class="feature-text">Lorem ipsum dolor sit amet, sed do eiusmod tempor incididunt quis nostrud exercitation</p>
      </div>
      <div class="feature">
        <div class="feature-icon">
          <svg width="22" height="22" viewBox="0 0 24 24" fill="none" stroke="#fff" stroke-width="2.4"><circle cx="12" cy="12" r="3.2"/><circle cx="12" cy="12" r="7.5" stroke-dasharray="3.6 2.3"/></svg>
        </div>
        <h3 class="feature-title">Icon text here</h3>
        <p class="feature-text">Lorem ipsum dolor sit amet, sed do eiusmod tempor incididunt quis nostrud exercitation</p>
      </div>
      <div class="feature">
        <div class="feature-icon">
          <svg width="22" height="22" viewBox="0 0 24 24" fill="none" stroke="#fff" stroke-width="2.4"><circle cx="12" cy="12" r="3.2"/><circle cx="12" cy="12" r="7.5" stroke-dasharray="3.6 2.3"/></svg>
        </div>
        <h3 class="feature-title">Icon text here</h3>
        <p class="feature-text">Lorem ipsum dolor sit amet, sed do eiusmod tempor incididunt quis nostrud exercitation</p>
      </div>
    </section>

    <footer class="footer">
      <p class="footer-label connect">Stay<br>connected<br>with us</p>
      <span class="footer-divider first"></span>
      <div class="social-list">
        <span class="social-name">Picfeed</span>
        <span class="social-name">Facenet</span>
        <span class="social-name">Homezy</span>
      </div>
      <span class="footer-divider second"></span>
      <p class="footer-label membership">Professional<br>membership</p>
      <span class="badge-round" role="img" aria-label="Professional membership badge"></span>
      <span class="badge-wide" role="img" aria-label="Industry association badge"></span>
    </footer>
  </main>
</body>
</html>
```